I need a SEO-friendly Wordpress website (making sure to style H1, H2, H3, etc correctly) for a Hawaii-based law firm called Meridian Crest Legal Group. Comparable websites include https://brvlaw.example/ and https://www.lomrit.example/ for design reference. The current copy on the TarnAdvocate.example website can be used.

```html
<!DOCTYPE html>
<html lang="en">
<head>
<meta charset="utf-8">
<title>Meridian Crest Legal Group</title>
<link href="https://fonts.googleapis.com/css2?family=Open+Sans:wght@400;600;700&display=swap" rel="stylesheet">
<style>
:root{
  --brown:#a4521b;
  --brown-dark:#8a4313;
  --orange:#dc6a21;
  --ink:#222;
  --text:#5a5a5a;
  --gray-bg:#efefef;
  --footer:#1d1d1d;
  --line:#d8d8d8;
}
*{box-sizing:border-box;margin:0;padding:0}
html,body{width:1200px;height:3360px;overflow:hidden}
body{font-family:'Open Sans',sans-serif;color:var(--ink);background:#fff;position:relative}
.abs{position:absolute}
a{color:inherit;text-decoration:none}

/* header */
.site-header{position:absolute;left:0;top:0;width:1200px;height:87px;background:#fff}
.brand{left:110px;top:20px;font-weight:700;font-size:19px;line-height:23px;letter-spacing:-.5px;color:#333;text-transform:uppercase}
.call{left:648px;top:26px;display:flex;align-items:center;gap:10px}
.call-ico{width:38px;height:38px;border-radius:50%;border:2px solid #ccc;display:flex;align-items:center;justify-content:center}
.call small{display:block;font-size:11px;color:#444}
.call strong{font-size:17px;font-weight:700;color:#222}
.search{left:858px;top:28px;width:231px;height:34px;display:flex;border:1px solid #999}
.search span{flex:1;font-size:14px;color:#777;padding:7px 8px}
.search i{width:35px;background:#333;display:flex;align-items:center;justify-content:center}
.main-nav{position:absolute;left:0;top:87px;width:1200px;height:38px;background:var(--brown);display:flex;justify-content:center;gap:36px;align-items:center}
.main-nav a{color:#fff;font-size:15px;font-weight:600}

/* hero */
.hero{position:absolute;left:0;top:125px;width:1200px;height:534px;background:linear-gradient(180deg,#5e6d3a 0%,#4a2a22 35%,#2a1a16 70%,#3a2a22 100%)}
.hero-band{position:absolute;left:0;bottom:0;width:100%;height:64px;background:linear-gradient(90deg,#8a4414,#b8641f 50%,#8a4414);display:flex;align-items:center;justify-content:center}
.hero-band h1{color:#fff;font-size:30px;font-weight:600;text-shadow:0 1px 2px rgba(0,0,0,.4)}

/* about */
.about{position:absolute;left:0;top:659px;width:1200px;height:532px}
.about h2{position:absolute;left:110px;top:74px;font-size:35px;font-weight:600;letter-spacing:-.5px}
.about h3{position:absolute;left:110px;top:131px;font-size:17px;font-weight:600}
.about .copy{position:absolute;left:110px;top:168px;width:490px;font-size:14.5px;line-height:28.5px;color:var(--text);text-align:justify}
.about .copy p+p{margin-top:11px}
.btn{display:inline-flex;align-items:center;justify-content:center;gap:8px;background:var(--brown);color:#fff;font-weight:700;font-size:14px;text-transform:uppercase}
.about .btn{position:absolute;left:110px;top:409px;width:149px;height:43px}
.practice{position:absolute;width:200px;text-align:center}
.practice .ring{width:120px;height:120px;border-radius:50%;border:2px solid var(--brown);margin:0 auto 12px;display:flex;align-items:center;justify-content:center}
.practice span{font-size:17px;font-weight:600}

/* cards */
.features{position:absolute;left:0;top:1191px;width:1200px;height:664px;background:var(--gray-bg)}
.card{position:absolute;top:83px;width:317px;height:500px;background:#fff;border:1px solid #ccc;box-shadow:0 1px 3px rgba(0,0,0,.1)}
.card .photo{position:absolute;left:9px;top:11px;width:299px;height:166px}
.card .photo b{position:absolute;left:0;bottom:0;width:100%;height:30px;background:rgba(150,70,20,.9);color:#fff;font-size:16px;font-weight:600;text-align:center;line-height:30px}
.card .select{position:absolute;left:17px;top:193px;width:283px;height:36px;border:1px solid #bbb;font-size:15px;font-weight:600;padding:7px 26px;display:flex;justify-content:space-between}
.card .select::after{content:"";position:absolute;right:32px;top:0;height:100%;border-left:1px solid #bbb}
.card h4{position:absolute;left:0;width:100%;top:206px;text-align:center;font-size:16px;font-weight:600}
.card p{position:absolute;left:16px;top:249px;width:285px;font-size:14.5px;line-height:27.5px;color:var(--text);text-align:justify}
.card hr{position:absolute;left:0;top:410px;width:100%;border:0;border-top:3px solid #e6e6e6}
.card .btn{position:absolute;left:50%;transform:translateX(-50%);top:439px;height:39px;padding:0 16px}

/* reasons */
.reasons{position:absolute;left:0;top:1855px;width:1200px;height:586px}
.reasons .kicker{position:absolute;left:110px;top:86px;font-size:16px;font-weight:600}
.reasons h2{position:absolute;left:110px;top:117px;font-size:31px;font-weight:600;letter-spacing:-.5px}
.reason{position:absolute;left:110px;width:505px}
.reason .ico{position:absolute;left:0;top:0;width:64px;height:64px;border-radius:50%;border:2px solid #e3e3e3;display:flex;align-items:center;justify-content:center}
.reason h3{margin-left:82px;font-size:17px;font-weight:600;text-transform:uppercase}
.reason p{margin-left:83px;margin-top:6px;font-size:14.5px;line-height:26px;color:var(--text);text-align:justify}
.reasons .team{position:absolute;left:649px;top:84px;width:440px;height:419px;background:linear-gradient(160deg,#dfe3e6,#9aa6ad 40%,#2a2e33 75%,#3d4148)}

/* blog */
.blog{position:absolute;left:0;top:2441px;width:1200px;height:551px;background:var(--gray-bg)}
.blog h2{position:absolute;left:0;width:100%;top:60px;text-align:center;font-size:33px;font-weight:600;letter-spacing:-.5px}
.post{position:absolute;left:179px;top:136px;width:842px;height:348px;background:#fff;box-shadow:0 1px 4px rgba(0,0,0,.12)}
.post .photo{position:absolute;left:31px;top:32px;width:323px;height:272px;background:linear-gradient(160deg,#e9ece8,#b7bfb4 45%,#3b4a3e 80%,#5b6258)}
.post h3{position:absolute;left:405px;top:46px;font-size:20px;font-weight:400;text-transform:uppercase}
.post .meta{position:absolute;left:406px;top:87px;display:flex;gap:26px;font-size:15px;color:var(--brown)}
.post .meta span{display:flex;align-items:center;gap:9px}
.post p{position:absolute;left:406px;top:130px;width:400px;font-size:15px;line-height:27.5px;color:#777}
.post .btn{position:absolute;left:406px;top:270px;width:120px;height:40px;background:var(--orange);font-weight:600}
.arrow{position:absolute;top:2720px;width:40px;height:40px;border-radius:50%;border:1px solid #666;background:#fff;display:flex;align-items:center;justify-content:center}

/* footer */
.site-footer{position:absolute;left:0;top:2992px;width:1200px;height:368px;background:linear-gradient(180deg,#242424,#1a1a1a 60%,#2b2b2b);color:#fff}
.site-footer h4{font-size:16px;font-weight:600;text-transform:uppercase;margin-bottom:20px}
.fcol{position:absolute;top:57px}
.fcol li{list-style:none;font-size:14.5px;line-height:30px}
.fcol li::before{content:"» ";}
.contact-row{display:flex;gap:10px;font-size:14.5px;line-height:23px;margin-bottom:10px}
.field{width:231px;height:32px;border:1px solid #ddd;font-size:14px;padding:6px 14px;margin-bottom:12px}
.send{width:83px;height:32px;background:var(--brown);font-size:14px;font-weight:700;display:flex;align-items:center;justify-content:center;margin-top:12px}
.fdivider{position:absolute;left:112px;top:305px;width:977px;border-top:1px solid #555}
.copyright{position:absolute;left:112px;top:327px;font-size:14px}
.social{position:absolute;left:934px;top:318px;display:flex;gap:6px}
.social i{width:34px;height:34px;border-radius:50%;border:1px solid #bbb;display:block}
</style>
</head>
<body>

<header class="site-header">
  <div class="abs brand">Meridian Crest<br>Legal Group</div>
  <div class="abs call">
    <div class="call-ico"><svg width="16" height="16" viewBox="0 0 24 24"><path fill="#a4521b" d="M6.6 10.8a15 15 0 0 0 6.6 6.6l2.2-2.2c.3-.3.7-.4 1-.2 1.1.4 2.3.6 3.6.6.6 0 1 .4 1 1V20c0 .6-.4 1-1 1A17 17 0 0 1 3 4c0-.6.4-1 1-1h3.5c.6 0 1 .4 1 1 0 1.3.2 2.5.6 3.6.1.3 0 .7-.2 1z"/></svg></div>
    <div><small>Call Us Today</small><strong>+1.808.555.0147</strong></div>
  </div>
  <div class="abs search"><span>Search</span><i><svg width="14" height="14" viewBox="0 0 24 24"><circle cx="10" cy="10" r="6.5" fill="none" stroke="#fff" stroke-width="3"/><path d="M15 15l6 6" stroke="#fff" stroke-width="3"/></svg></i></div>
</header>
<nav class="main-nav">
  <a>Home</a><a>About Us</a><a>Practice Areas</a><a>Attorneys</a><a>Blog</a><a>Contact Us</a>
</nav>

<section class="hero" role="img" aria-label="Group portrait of the firm's five attorneys in a wood-panelled conference room">
  <div class="hero-band"><h1>Divorce and Personal Injury Lawyers</h1></div>
</section>

<section class="about">
  <h2>ABOUT US</h2>
  <h3>Lawyers Serving the Big Island and Neighboring Islands</h3>
  <div class="copy">
    <p>The experienced attorneys in the Meridian Crest Legal Group's Waimea Bay, Hawaii office provide clients with a wide range of litigation expertise, including legal claims involving divorce &amp; family, personal injury, toxic exposures, intellectual property, and real estate.</p>
    <p>Our Waimea office also offers commercial and hospitality litigation expertise on behalf of a wide variety of clients, including restaurants, hotels, property owners, and many others.</p>
  </div>
  <a class="btn">Learn More <svg width="14" height="14" viewBox="0 0 24 24"><circle cx="12" cy="12" r="10" fill="none" stroke="#fff" stroke-width="2.5"/><path d="M10 7l5 5-5 5" fill="none" stroke="#fff" stroke-width="2.5"/></svg></a>

  <div class="practice" style="left:645px;top:100px">
    <div class="ring"><svg width="60" height="60" viewBox="0 0 60 60" fill="none" stroke="#333" stroke-width="2"><circle cx="30" cy="14" r="6"/><path d="M20 40V26h20v14M24 26v14M36 26v14M6 46h14l10 6 24-10"/><path d="M6 40h12"/></svg></div>
    <span>Personal Injury</span>
  </div>
  <div class="practice" style="left:868px;top:100px">
    <div class="ring"><svg width="64" height="60" viewBox="0 0 64 60" fill="none" stroke="#333" stroke-width="2"><circle cx="18" cy="12" r="6"/><circle cx="46" cy="12" r="6"/><path d="M8 32v-6a10 10 0 0 1 20 0v6M36 32v-6a10 10 0 0 1 20 0v6M4 34h24M36 34h24M32 30v22M14 52h36"/></svg></div>
    <span>Family &amp; Divorce</span>
  </div>
  <div class="practice" style="left:765px;top:272px">
    <div class="ring"><svg width="60" height="60" viewBox="0 0 60 60" fill="none" stroke="#333" stroke-width="2"><circle cx="16" cy="12" r="5"/><circle cx="44" cy="12" r="5"/><circle cx="30" cy="28" r="4"/><path d="M8 36V24h16v10M36 34V24h16v12M24 42h12M6 38l10 14M54 38l-10 14M26 36h8v8h-8z"/></svg></div>
    <span>Child Custody</span>
  </div>
</section>

<section class="features">
  <article class="card" style="left:110px">
    <div class="photo" role="img" aria-label="Attorney in a suit signing papers at a desk" style="background:linear-gradient(160deg,#cfd6da,#8d9aa3 45%,#2d3238)"><b>Areas of Practice</b></div>
    <div class="select"><span>Family &amp; Divorce</span><svg width="10" height="36" viewBox="0 0 10 36" style="margin:-7px -14px 0 0"><path d="M1 16h8l-4 5z" fill="#222"/></svg></div>
    <p>Our lawyers handle all aspects of family law on the Big Island and neighboring islands. We have more than 70 years of combined experience handling divorce, custody, and all aspects of family law.</p>
    <hr>
    <a class="btn">View Practices</a>
  </article>
  <article class="card" style="left:441px">
    <div class="photo" role="img" aria-label="Attorneys meeting around a conference table, seen from above" style="background:linear-gradient(160deg,#6b5a48,#4b3226 45%,#7b4a2a)"><b>Attorneys</b></div>
    <div class="select"><span>Daniel Okafor, Esq.</span><svg width="10" height="36" viewBox="0 0 10 36" style="margin:-7px -14px 0 0"><path d="M1 16h8l-4 5z" fill="#222"/></svg></div>
    <p>Daniel Okafor graduated from the Harborview University, Cliffside College of the Law, in 1972. He graduated magna cum laude from Westbrook University College of Law in 2008 receiving an LLM.</p>
    <hr>
    <a class="btn">View Attorneys</a>
  </article>
  <article class="card" style="left:772px">
    <div class="photo" role="img" aria-label="Attorney in a grey suit speaking with two clients" style="background:linear-gradient(160deg,#c28450,#9a6a48 40%,#5a5c66)"><b>Careers</b></div>
    <h4>Join Our Tradition of Excellence</h4>
    <p>Sed ut perspiciatis unde omnis iste natus error sit voluptatem accusantium doloremque laudantium, totam rem aperiam, eaque ipsa quae ab illo inventore veritatis et quasi architecto.</p>
    <hr>
    <a class="btn">View Careers</a>
  </article>
</section>

<section class="reasons">
  <div class="kicker">WHY CHOOSE MERIDIAN CREST LEGAL GROUP</div>
  <h2>3 REASONS TO HIRE US</h2>
  <div class="reason" style="top:187px">
    <div class="ico"><svg width="34" height="30" viewBox="0 0 34 30" fill="none" stroke="#a4521b" stroke-width="3"><rect x="2" y="8" width="30" height="20"/><path d="M12 8V3h10v5M2 16h30M15 16v4h4v-4"/></svg></div>
    <h3>Experienced</h3>
    <p>Our lawyers are board-certified specialists in all fields of our practice. With over 70 combined years experience, you're in good hands with us</p>
  </div>
  <div class="reason" style="top:318px">
    <div class="ico"><svg width="34" height="34" viewBox="0 0 34 34" fill="none" stroke="#a4521b" stroke-width="2"><circle cx="17" cy="12" r="4"/><path d="M10 12a7 7 0 0 1 14 0M6 12a11 11 0 0 1 22 0M14 30l1-12h4l1 12z"/><path d="M5 26l1.5 3M29 26l-1.5 3"/></svg></div>
    <h3>Focused On You</h3>
    <p>Nemo enim ipsam voluptatem quia voluptas sit aspernatur aut odit aut fugit, sed quia consequuntur</p>
  </div>
  <div class="reason" style="top:422px">
    <div class="ico"><svg width="34" height="30" viewBox="0 0 34 30" fill="none" stroke="#a4521b" stroke-width="2.5"><rect x="2" y="2" width="30" height="26"/><path d="M2 8h30M8 24l-2-10 6 5 5-7 5 7 6-5-2 10z"/></svg></div>
    <h3>Reputation</h3>
    <p>Nam libero tempore, cum soluta nobis est eligendi optio cumque nihil impedit quo minus id quod</p>
  </div>
  <div class="team" role="img" aria-label="Team of lawyers working together around a table with laptops, seen from above"></div>
</section>

<section class="blog">
  <h2>OUR BLOG</h2>
  <article class="post">
    <div class="photo" role="img" aria-label="Attorney reviewing a document with a couple in a bright office"></div>
    <h3>Make Every Effort to Make It Work</h3>
    <div class="meta">
      <span><svg width="15" height="15" viewBox="0 0 24 24" fill="none" stroke="#a4521b" stroke-width="2"><rect x="3" y="5" width="18" height="16"/><path d="M3 10h18M8 3v4M16 3v4"/></svg>March 25 2019</span>
      <span><svg width="16" height="14" viewBox="0 0 24 20" fill="none" stroke="#a4521b" stroke-width="2"><ellipse cx="12" cy="9" rx="10" ry="7"/><path d="M6 15l-2 4 6-3"/></svg>2 Comments</span>
    </div>
    <p>It might seem obvious, but far too many people forget that great relationships take hard work. Perhaps your relationship has gone through recent strain, or you're having a hard time finding that</p>
    <a class="btn">Read More</a>
  </article>
</section>
<div class="arrow" style="left:35px"><svg width="12" height="14" viewBox="0 0 12 14"><path d="M8 2L3 7l5 5" fill="none" stroke="#222" stroke-width="2"/></svg></div>
<div class="arrow" style="left:1124px"><svg width="12" height="14" viewBox="0 0 12 14"><path d="M4 2l5 5-5 5" fill="none" stroke="#222" stroke-width="2"/></svg></div>

<footer class="site-footer">
  <div class="fcol" style="left:112px">
    <h4>Company</h4>
    <ul><li>Home</li><li>Practice Areas</li><li>Attorneys</li><li>Blog</li><li>Contact Us</li></ul>
  </div>
  <div class="fcol" style="left:318px">
    <h4>Practice Areas</h4>
    <ul><li>Family &amp; Divorce</li><li>Personal Injury</li><li>Corporate &amp; IP</li><li>Real Estate</li></ul>
  </div>
  <div class="fcol" style="left:553px">
    <h4>Contact Us</h4>
    <div class="contact-row"><svg width="12" height="16" viewBox="0 0 12 16" style="margin-top:4px"><path d="M6 0a6 6 0 0 1 6 6c0 4-6 10-6 10S0 10 0 6a6 6 0 0 1 6-6z" fill="#fff"/><circle cx="6" cy="6" r="2" fill="#222"/></svg><span>48-210 Lanakila Way Suite 12<br>Waimea Bay, Hawaii 96799</span></div>
    <div class="contact-row"><svg width="13" height="13" viewBox="0 0 24 24" style="margin-top:5px"><path fill="#fff" d="M6.6 10.8a15 15 0 0 0 6.6 6.6l2.2-2.2c.3-.3.7-.4 1-.2 1.1.4 2.3.6 3.6.6.6 0 1 .4 1 1V20c0 .6-.4 1-1 1A17 17 0 0 1 3 4c0-.6.4-1 1-1h3.5c.6 0 1 .4 1 1 0 1.3.2 2.5.6 3.6.1.3 0 .7-.2 1z"/></svg><span>1.808.555.0147</span></div>
    <div class="contact-row"><svg width="14" height="12" viewBox="0 0 24 18" style="margin-top:6px"><rect x="1" y="1" width="22" height="16" fill="none" stroke="#fff" stroke-width="2"/><path d="M1 1l11 9 11-9" fill="none" stroke="#fff" stroke-width="2"/></svg><span>clients@tarnadvocate.example</span></div>
  </div>
  <div class="fcol" style="left:858px">
    <h4>Get In Touch</h4>
    <div class="field">Enter Your Name</div>
    <div class="field">Enter Email Address</div>
    <div class="field">Enter Phone Number</div>
    <div class="send">SEND</div>
  </div>
  <div class="fdivider"></div>
  <div class="copyright">© 2019 Meridian Crest Legal Group. All Rights Reserved</div>
  <div class="social"><i></i><i></i><i></i><i></i></div>
</footer>

</body>
</html>
```